Veranix - Solution provider in business consulting

Veranix is a swiss based company providing solutions for developing markets. The business covers various fields of business consulting, such as supply chain, product costs, quality management and manufacturing management. The Business operates in a efficient, straight and solution oriented manner.
The final design should communicate these characteristics. Asian people as well as as western people shall identify the qualities of the company at first sight.
The customer needs business cards with a simple view but an recognizable design, printed in high quality. Engraved elements such as the globe or simple words are possible.
Available colors are: (RAL)
102/102/102
51/102/102
153/204/153
255/102/51
Font: Calibri

```html
<!DOCTYPE html>
<html lang="en">
<head>
<meta charset="utf-8">
<title>Veranix – Business Card</title>
<link href="https://fonts.googleapis.com/css2?family=Carlito:wght@400;700&display=swap" rel="stylesheet">
<style>
  :root {
    --paper: #ffffff;
    --slate: #40454d;
    --mint: #c9e6d4;
    --stone: #666666;
    --light: #ffffff;
    --mark: #222222;
  }
  * { margin: 0; padding: 0; box-sizing: border-box; }
  html, body { width: 1200px; height: 843px; overflow: hidden; background: var(--paper); }
  body { position: relative; font-family: "Carlito", "Calibri", sans-serif; }

  .crop-marks { position: absolute; inset: 0; }

  .card {
    position: absolute; left: 98px; top: 132px; width: 1001px; height: 573px;
    background: var(--slate); overflow: hidden;
  }
  .card__edge {
    position: absolute; right: 0; top: 0; width: 34px; height: 100%;
    background: var(--mint);
  }
  .brand-band {
    position: absolute; left: 0; top: 207px; width: 440px; height: 158px;
    background: var(--mint);
    display: flex; align-items: center; justify-content: center; gap: 18px;
  }
  .brand-band__name {
    font-size: 72px; font-weight: 400; color: var(--stone); letter-spacing: 1px;
  }
  .brand-band__dot {
    width: 46px; height: 46px; border-radius: 50%; background: var(--stone);
  }

  .address {
    position: absolute; right: 580px; top: 420px; text-align: right;
    color: var(--light); font-size: 26px; line-height: 31px;
  }

  .website {
    position: absolute; left: 485px; top: 286px; width: 0; height: 0;
  }
  .website span {
    position: absolute; left: 0; top: 0;
    transform: translate(-50%, -50%) rotate(-90deg);
    white-space: nowrap; color: var(--light); font-size: 43px; letter-spacing: 0.5px;
  }

  .person {
    position: absolute; right: 100px; top: 76px; text-align: right; color: var(--light);
  }
  .person__name { font-size: 33px; font-weight: 700; line-height: 40px; }
  .person__role { font-size: 33px; font-weight: 400; line-height: 40px; }

  .contact {
    position: absolute; right: 100px; top: 418px; color: var(--light);
    font-size: 28px; list-style: none;
  }
  .contact li {
    display: flex; align-items: center; justify-content: flex-end; gap: 16px;
    height: 34px;
  }
  .contact svg { width: 26px; height: 26px; fill: none; stroke: var(--light); stroke-width: 1.8; }
  .contact .icon-phone { fill: var(--light); stroke: none; }
</style>
</head>
<body>
  <svg class="crop-marks" width="1200" height="843" viewBox="0 0 1200 843" aria-hidden="true">
    <g stroke="var(--mark)" stroke-width="1">
      <line x1="84" y1="0" x2="84" y2="72"/>
      <line x1="117" y1="36" x2="117" y2="93"/>
      <line x1="0" y1="84" x2="72" y2="84"/>
      <line x1="36" y1="117" x2="93" y2="117"/>
      <line x1="1082" y1="36" x2="1082" y2="93"/>
      <line x1="1115" y1="0" x2="1115" y2="72"/>
      <line x1="1107" y1="117" x2="1164" y2="117"/>
      <line x1="1128" y1="84" x2="1200" y2="84"/>
      <line x1="84" y1="771" x2="84" y2="843"/>
      <line x1="117" y1="750" x2="117" y2="807"/>
      <line x1="0" y1="759" x2="72" y2="759"/>
      <line x1="36" y1="726" x2="93" y2="726"/>
      <line x1="1082" y1="750" x2="1082" y2="807"/>
      <line x1="1115" y1="771" x2="1115" y2="843"/>
      <line x1="1107" y1="726" x2="1164" y2="726"/>
      <line x1="1128" y1="759" x2="1200" y2="759"/>
    </g>
  </svg>

  <section class="card">
    <div class="card__edge"></div>

    <div class="brand-band">
      <span class="brand-band__name">veranix</span>
      <span class="brand-band__dot"></span>
    </div>

    <address class="address" style="font-style: normal;">
      Veranix GmbH<br>
      Lindenweg 18<br>
      9240 Uzwil<br>
      Switzerland
    </address>

    <div class="website"><span>www.veranix.ch</span></div>

    <div class="person">
      <div class="person__name">Marco Keller</div>
      <div class="person__role">CEO</div>
    </div>

    <ul class="contact">
      <li>
        <svg viewBox="0 0 26 26" aria-hidden="true"><rect x="7" y="3" width="12" height="20" rx="2" transform="rotate(-15 13 13)"/></svg>
        <span>+41 79 555 0182</span>
      </li>
      <li>
        <svg viewBox="0 0 26 26" aria-hidden="true"><path class="icon-phone" d="M6 4l5 0 1 6-3 2c1 3 3 5 6 6l2-3 6 1 0 5c-10 1-18-7-17-17z"/></svg>
        <span>+41 71 555 0347</span>
      </li>
      <li>
        <svg viewBox="0 0 26 26" aria-hidden="true"><path d="M3 11l10-7 10 7v11H3z M3 11l10 7 10-7 M3 22l7-6 M23 22l-7-6"/></svg>
        <span>marco.keller@veranix.ch</span>
      </li>
    </ul>
  </section>
</body>
</html>
```